Online business manager needs a website

I need a website designed and then coded. I am an online business manager serving a number of different industries providing administrative support to existing small businesses and helping solo practitioners get their new business up and running.

I didn't have a logo formally designed but have been using the attached avatar and wouldn't mind something that incorporated that.

The business doesn't have an official name, so I've just been using my name Lena Morvath, Online Business Manager or Lena Morvath, OBM. I've attached two documents that I have made previously for an example of content.

I would prefer the final site be in Wordpress.

Requirements
Must have
• A way to contact me, testimonials, list of services

```html
<!DOCTYPE html>
<html lang="en">
<head>
<meta charset="utf-8">
<title>Lena Morvath OBM</title>
<link href="https://fonts.googleapis.com/css2?family=Poppins:wght@400;500;600;700;800&family=Lato:wght@400;700&family=Michroma&display=swap" rel="stylesheet">
<style>
:root{
  --purple:#5a3788;
  --band:#5d3f80;
  --ink:#1e1e1e;
  --hero-dark:#271c3b;
  --hero-glow:#5b4fc2;
  --night:#0c0b26;
  --mist:#ece8f0;
  --white:#ffffff;
  --star:#f4cf1a;
}
*{margin:0;padding:0;box-sizing:border-box}
html,body{width:1200px;height:3897px;overflow:hidden}
body{position:relative;background:var(--white);font-family:'Poppins',sans-serif;color:var(--ink)}
.abs{position:absolute}

/* header */
.site-header{left:0;top:0;width:1200px;height:74px;background:var(--white)}
.brand{left:112px;top:12px;font-weight:800;font-size:29px;line-height:27px;color:var(--purple);letter-spacing:-.5px}
.main-nav{top:28px;display:flex;font-weight:600;font-size:16px}
.main-nav span{position:absolute;white-space:nowrap}

/* hero */
.hero{left:0;top:74px;width:1200px;height:586px;background:linear-gradient(100deg,var(--hero-dark) 0%,var(--hero-dark) 38%,#3b2f78 65%,var(--hero-glow) 100%)}
.hero-visual{left:575px;top:74px;width:625px;height:586px;background:radial-gradient(ellipse at 60% 40%,rgba(140,130,255,.55),rgba(60,45,130,.2) 60%,transparent 80%)}
.hero-title{left:112px;top:232px;font-weight:800;font-size:70px;line-height:69px;color:var(--white);letter-spacing:-1px}

/* about */
.about-frame{left:76px;top:797px;width:540px;height:419px;background:var(--purple)}
.about-photo{left:110px;top:828px;width:475px;height:351px;background:linear-gradient(135deg,#b8467a,#e7c0b0 50%,#3c4a2a)}
.about-title{left:670px;top:795px;font-weight:800;font-size:42px;color:var(--purple)}
.about-card{left:522px;top:879px;width:566px;height:405px;background:var(--white);box-shadow:0 2px 14px rgba(0,0,0,.14)}
.about-text{left:578px;top:925px;width:455px;font-family:'Lato',sans-serif;font-size:14.6px;line-height:30px;color:#3d3d3d;text-align:justify}
.btn-read{left:899px;top:1210px;width:133px;height:37px;background:var(--purple);color:var(--white);font-weight:700;font-size:15px;display:flex;align-items:center;justify-content:center}

/* services */
.services{left:0;top:1393px;width:1200px;height:869px;background:var(--band)}
.section-title{width:1200px;left:0;text-align:center;font-weight:800;font-size:42px}
.service-card{width:462px;height:206px;border:2.5px solid var(--white);border-radius:18px}
.service-card h3{position:absolute;left:40px;right:40px;top:-13px;text-align:center;font-family:'Michroma',sans-serif;font-weight:400;font-size:14px;line-height:20px;letter-spacing:1px;color:var(--white)}
.service-card h3 span{background:var(--band);padding:0 18px}
.service-card ul{position:absolute;left:27px;top:50px;list-style:none;color:var(--white);font-size:15.5px;line-height:27.5px}
.service-img{position:absolute;left:276px;top:38px;width:160px;height:134px;border-radius:4px}

/* testimonials */
.testimonials{left:0;top:2262px;width:1200px;height:587px;background:var(--mist)}
.quote-side{top:2493px;width:220px;height:185px;background:var(--white);opacity:.45;box-shadow:0 2px 8px rgba(0,0,0,.08)}
.quote-side p{position:absolute;top:45px;font-size:10.5px;line-height:21px;color:#777;text-align:center;width:190px}
.quote-side .stars{position:absolute;top:16px;font-size:15px;color:var(--star)}
.quote-side .who{position:absolute;top:137px;font-size:11px;font-weight:600;color:#555}
.quote-side .dot{position:absolute;top:120px;width:54px;height:54px;border-radius:50%;background:#cfc6c0}
.quote-main{left:333px;top:2454px;width:545px;height:257px;background:var(--white);box-shadow:0 3px 14px rgba(0,0,0,.15)}
.quote-main .stars{position:absolute;top:16px;width:100%;text-align:center;font-size:26px;color:var(--star);letter-spacing:1px}
.quote-main p{position:absolute;left:60px;top:60px;width:425px;text-align:center;font-family:'Lato',sans-serif;font-size:15px;line-height:21px;color:#2a2a2a}
.avatar{left:371px;top:2611px;width:74px;height:74px;border-radius:50%;background:linear-gradient(135deg,#8a5a3c,#d4a37c)}
.quote-name{left:478px;top:2645px;font-weight:700;font-size:14px;color:#222}
.dots{left:598px;top:2757px;display:flex;gap:3px}
.dots i{width:8px;height:8px;border-radius:50%;background:#9b9b9b}

/* contact */
.contact{left:0;top:2849px;width:1200px;height:729px;background:radial-gradient(ellipse at 78% 85%,#5a1fb8 0%,rgba(70,30,150,.5) 30%,transparent 60%),radial-gradient(ellipse at 25% 95%,#3b2a9a 0%,transparent 45%),var(--night)}
.form-box{left:180px;top:3124px;width:439px;height:345px;background:var(--band)}
.field{left:204px;width:371px;height:56px;background:var(--white);font-family:'Lato',sans-serif;font-size:17px;color:#333;padding:0 21px;display:flex;align-items:center}
.submit{left:180px;width:439px;top:3402px;text-align:center;color:var(--white);font-family:'Lato',sans-serif;font-size:19px;text-decoration:underline}
.info-label{left:707px;font-weight:700;font-size:20px;color:var(--white)}
.info-value{left:707px;font-family:'Lato',sans-serif;font-size:15.5px;color:var(--white)}

/* footer */
.site-footer{left:0;top:3578px;width:1200px;height:319px;background:#000}
.footer-brand{left:0;width:1200px;top:3660px;text-align:center;font-weight:800;font-size:30px;line-height:29px;color:var(--white)}
.footer-nav{top:3742px;font-weight:600;font-size:16px;color:var(--white)}
.footer-nav span{position:absolute;white-space:nowrap}
.social{left:512px;top:3807px;display:flex;gap:33px}
.social i{width:13px;height:13px;border-radius:50%;background:var(--white)}
.footer-rule{left:121px;top:3844px;width:972px;height:1px;background:#777}
.copyright{left:124px;top:3864px;font-size:14px;color:var(--white)}
</style>
</head>
<body>

<header class="abs site-header">
  <div class="abs brand">Lena Morvath<br>OBM</div>
  <nav class="abs main-nav">
    <span style="left:534px">HOME</span>
    <span style="left:610px">ABOUT</span>
    <span style="left:713px">SERVICES</span>
    <span style="left:831px">TESTIMONIAL</span>
    <span style="left:977px">CONTACT US</span>
  </nav>
</header>

<section class="abs hero"></section>
<div class="abs hero-visual" role="img" aria-label="Hands on a laptop with a glowing digital checklist"></div>
<h1 class="abs hero-title">welcome to<br>Lena Morvath<br>OBM</h1>

<div class="abs about-frame"></div>
<div class="abs about-photo" role="img" aria-label="Portrait of Lena Morvath in front of flowering shrubs"></div>
<h2 class="abs about-title">ABOUT ME</h2>
<div class="abs about-card"></div>
<p class="abs about-text">Hi! I'm so excited that you have chosen to explore my portfolio. Helping businesses achieve their goals is my passion, and I'm thrilled that with my assistance you will have more time for your own passion project. I thrive while working independently, which means you can be confident when leaving tasks for me. The type of work that lights me up is anything involving organization and/or spreadsheets. You need data analyzed that includes multiple nested if formulas? You have an overwhelming amount of email to sort through and appointments to book? I'm your gal!</p>
<div class="abs btn-read">READ MORE</div>

<section class="abs services"></section>
<h2 class="abs section-title" style="top:1508px;color:var(--white)">OUR SERVICES</h2>

<div class="abs service-card" style="left:112px;top:1639px">
  <h3><span>VIRTUAL ASSISTANCE</span></h3>
  <ul><li>Calendar Management</li><li>Email Management</li><li>Light Graphic Design</li><li>Data Entry</li></ul>
  <div class="service-img" role="img" aria-label="Laptop on a white desk" style="background:linear-gradient(135deg,#e8e8ea,#9a9ca2 55%,#d8d8dc)"></div>
</div>
<div class="abs service-card" style="left:626px;top:1639px">
  <h3><span>SOCIAL MEDIA &amp; CONTENT MANAGEMENT</span></h3>
  <ul><li>Content Repurposing</li><li>Graphics Creation</li><li>Audiogram Creation</li><li>Search Engine Optimization</li></ul>
  <div class="service-img" role="img" aria-label="Typewritten note about writing and editing" style="background:linear-gradient(135deg,#f2f0ea,#dcd8cc)"></div>
</div>
<div class="abs service-card" style="left:112px;top:1917px">
  <h3><span>FINANCE MANAGEMENT</span></h3>
  <ul style="left:31px"><li>Create Invoices</li><li>Track Receivables</li><li>Analyze Expense</li><li>Year Over Year Analytics</li></ul>
  <div class="service-img" role="img" aria-label="Desk with calculator, keyboard and paperwork" style="background:linear-gradient(135deg,#8fd0d8,#e9ecec 55%,#7bc3cc)"></div>
</div>
<div class="abs service-card" style="left:626px;top:1917px">
  <h3><span>BUSINESS MANAGEMENT</span></h3>
  <ul><li>Creation of Operating</li><li>Review of Website Strategy</li><li>Reporting and Analytics</li><li>Project Management</li></ul>
  <div class="service-img" role="img" aria-label="Two colleagues at laptops beside a wall of sticky notes" style="background:linear-gradient(135deg,#5fa8a0,#e4c75a 40%,#d9d4cf)"></div>
</div>

<section class="abs testimonials"></section>
<h2 class="abs section-title" style="top:2348px;color:#2e2e2e;font-size:43px">TESTIMONIALS</h2>

<div class="abs quote-side" style="left:121px">
  <span class="stars" style="left:160px">★★★★</span>
  <p style="left:25px">Clear updates every week and quick replies made our busy launch feel calm</p>
  <div class="dot" style="left:25px"></div>
  <span class="who" style="left:104px">MARCO</span>
</div>
<div class="abs quote-side" style="left:875px">
  <span class="stars" style="left:5px">★★★★</span>
  <p style="left:5px">Organized, reliable and kind, she kept our books and inbox in order</p>
  <span class="who" style="left:34px">TEO ALVIK</span>
  <div class="dot" style="left:140px"></div>
</div>

<div class="abs quote-main">
  <div class="stars">★★★★★</div>
  <p>When it became apparent that a project would take more time than I had, Lena stepped up to take on the required re-search. She was thorough and timely; able to meet a last-minute 12-hour deadline. I would highly recommend Lena to assist with your next project.</p>
</div>
<div class="abs avatar" role="img" aria-label="Client portrait"></div>
<div class="abs quote-name">DARA P. OWNER, NORTHGATE RENOVATIONS</div>
<div class="abs dots"><i></i><i></i><i></i></div>

<section class="abs contact"></section>
<h2 class="abs section-title" style="top:2967px;color:var(--white)">CONTACT US</h2>
<div class="abs form-box"></div>
<div class="abs field" style="top:3182px">Enter name</div>
<div class="abs field" style="top:3256px">Phone</div>
<div class="abs field" style="top:3332px">Email</div>
<div class="abs submit">SUBMIT</div>

<div class="abs info-label" style="top:3138px">FACEBOOK</div>
<div class="abs info-value" style="top:3182px">/LenaMorvathOBM</div>
<div class="abs info-label" style="top:3224px">LINKEDIN</div>
<div class="abs info-value" style="top:3250px">Lena Morvath</div>
<div class="abs info-label" style="top:3306px;left:710px">PHONE:</div>
<div class="abs info-value" style="top:3347px">555.210.4836</div>
<div class="abs info-label" style="top:3391px;left:711px">EMAIL:</div>
<div class="abs info-value" style="top:3435px;left:711px">lena.morvath@example.com</div>

<footer class="abs site-footer"></footer>
<div class="abs footer-brand">Lena Morvath<br>OBM</div>
<nav class="abs footer-nav">
  <span style="left:338px">HOME</span>
  <span style="left:408px">ABOUT</span>
  <span style="left:500px">SERVICES</span>
  <span style="left:618px">TESTIMONIAL</span>
  <span style="left:763px">CONTACT US</span>
</nav>
<div class="abs social"><i></i><i></i><i></i><i></i><i></i></div>
<div class="abs footer-rule"></div>
<div class="abs copyright">© 2023 Lena Morvath OBM</div>

</body>
</html>
```